Financial Advisor Resource Firm needs business card design

Need business card design for company in Omaha NE called Meridale Circle. We provide resources to financial advisors....workshop programs, retirement analysis, and insurance planning. I would like to see designs that use grays, greens, black, and white colors. The final design should communicate 'collaboration' and be simple yet attractive to financial planning clients. I will attached our logo and another picture of a puzzle piece coming together. I would like the incorporate the puzzle picture somehow, maybe on the back somehow, with color or just the gray scale....OR, the picture be the front of the card with 'Meridale' definition on it (see upload) and then company logo, employee name, title, address on the back (see ppt uploaded). The following disclosure needs to be included somewhere- Advisory services offered through Stonebrook Assets, LLC.
Updates

I uploaded a svg and ai file of the logo

Target Market(s)

Financial planning clients and financial advisors....so pretty diverse age range of about 40-70.

Industry/Entity Type

Financial Planning

Contact Information for Business Card

Tobias L. Fenwright, MBA
Founder/President
5287 E. Larkin Road
Suite 230
Omaha, NE 68190
Phone- (402) 555-0147
Cell- (402) 555-0183
Fax- (402) 555-0129
email- tobias@meridaleplan.example
web address- www.meridaleplan.example

Colors
1b1b1b
474747
d3d3d3
ffffff
9bcb3c
abd036

Requirements
Must have
• Must include logo provided, must be 2 sided, and must have disclosure...all of these items listed in project description

```html
<!DOCTYPE html>
<html lang="en">
<head>
<meta charset="utf-8">
<title>Meridale Circle – Business Card</title>
<link href="https://fonts.googleapis.com/css2?family=Poppins:wght@300;400;600&display=swap" rel="stylesheet">
<style>
  :root {
    --ink: #1b1b1b;
    --charcoal: #2b2b2b;
    --slate: #474747;
    --mist: #d3d3d3;
    --paper: #ffffff;
    --leaf: #9bcb3c;
    --lime: #abd036;
    --stage: #ececec;
  }
  * { margin: 0; padding: 0; box-sizing: border-box; }
  html, body { width: 1200px; height: 862px; overflow: hidden; }
  body {
    background: var(--stage);
    font-family: "Poppins", sans-serif;
    display: flex;
    flex-direction: column;
    align-items: center;
    justify-content: center;
    gap: 40px;
  }
  .card {
    position: relative;
    width: 630px;
    height: 360px;
    border-radius: 4px;
    overflow: hidden;
    box-shadow: 0 6px 18px rgba(0,0,0,0.18);
  }

  /* Back side */
  .card-back { background: var(--charcoal); color: var(--paper); }
  .brand {
    display: flex;
    align-items: center;
    gap: 12px;
    font-weight: 400;
    letter-spacing: 1px;
  }
  .brand-dot { width: 22px; height: 22px; border-radius: 50%; background: var(--leaf); flex: none; }
  .card-back .brand {
    position: absolute;
    left: 50%; top: 128px;
    transform: translateX(-50%);
    font-size: 40px;
    color: var(--paper);
    white-space: nowrap;
  }
  .back-address {
    position: absolute;
    left: 0; right: 0; bottom: 70px;
    display: flex; justify-content: center; align-items: center; gap: 8px;
    font-size: 14px; font-weight: 300;
  }
  .back-address svg { width: 12px; height: 16px; }
  .disclosure {
    position: absolute;
    left: 0; right: 0; bottom: 22px;
    text-align: center;
    font-size: 9.5px; font-weight: 300;
    color: var(--mist);
    letter-spacing: 0.3px;
  }

  /* Front side */
  .card-front { background: var(--paper); color: var(--slate); }
  .card-front .brand {
    position: absolute;
    left: 34px; top: 140px;
    font-size: 28px;
    color: var(--ink);
    white-space: nowrap;
  }
  .card-front .brand-dot { width: 18px; height: 18px; }
  .contact {
    position: absolute;
    left: 360px; top: 36px;
    padding-left: 18px;
    border-left: 1.5px solid var(--leaf);
    height: 186px;
  }
  .contact-name { color: var(--leaf); font-weight: 600; font-size: 17px; letter-spacing: 0.5px; text-transform: uppercase; white-space: nowrap; }
  .contact-title { font-size: 12px; margin: 2px 0 10px; font-weight: 300; color: var(--slate); }
  .contact-list { list-style: none; font-size: 12.5px; line-height: 21px; font-weight: 300; color: var(--ink); }
  .contact-list li { display: flex; align-items: center; gap: 10px; white-space: nowrap; }
  .contact-list svg { width: 12px; height: 12px; flex: none; fill: var(--leaf); }
  .web-accent { color: var(--leaf); }
  .swoosh { position: absolute; left: 0; top: 0; width: 630px; height: 360px; }
</style>
</head>
<body>

  <section class="card card-back">
    <div class="brand"><span class="brand-dot"></span>Meridale Circle</div>
    <p class="back-address">
      <svg viewBox="0 0 12 16" aria-hidden="true"><path fill="#9bcb3c" d="M6 0a6 6 0 0 0-6 6c0 4.5 6 10 6 10s6-5.5 6-10a6 6 0 0 0-6-6zm0 8.5A2.5 2.5 0 1 1 6 3.5a2.5 2.5 0 0 1 0 5z"/></svg>
      5287 E. Larkin Road Suite 230
    </p>
    <p class="disclosure">Advisory services offered through Stonebrook Assets, LLC.</p>
  </section>

  <section class="card card-front">
    <div class="brand"><span class="brand-dot"></span>Meridale Circle</div>

    <div class="contact">
      <h1 class="contact-name">Tobias L. Fenwright, MBA</h1>
      <p class="contact-title">Founder | President</p>
      <ul class="contact-list">
        <li><svg viewBox="0 0 12 12"><path d="M2.5 0l2 2.5-1.2 1.5a7 7 0 0 0 4.7 4.7L9.5 7.5 12 9.5 10.5 12C4.5 12 0 7.5 0 1.5z"/></svg>(402) 555-0147</li>
        <li><svg viewBox="0 0 12 12"><path d="M3 0h6v12H3zm1 1v8h4V1z"/></svg>(402) 555-0183</li>
        <li><svg viewBox="0 0 12 12"><path d="M3 0h6v3H3zM0 4h12v6h-2v2H2v-2H0zm3 4v3h6V8z"/></svg>(402) 555-0129</li>
        <li><svg viewBox="0 0 12 12"><path d="M0 2h12v8H0zm1 1v.5l5 3.5 5-3.5V3z"/></svg>tobias@meridaleplan.example</li>
        <li><svg viewBox="0 0 12 12"><circle cx="6" cy="6" r="6"/></svg><span>www.<span class="web-accent">meridaleplan.example</span></span></li>
      </ul>
    </div>

    <svg class="swoosh" viewBox="0 0 630 360" aria-hidden="true">
      <path fill="var(--leaf)" d="M0 340 Q370 326 630 210 L630 222 Q390 334 0 347 Z"/>
      <path fill="var(--ink)" d="M0 352 Q400 342 630 232 L630 360 L0 360 Z"/>
    </svg>
  </section>

</body>
</html>
```